Equipment Finance Specialist I work with companies who need the funds to buy their equipment

I would like a business card that stands out on the shelves. I want to be able to hand it to someone and say WOW. This card should have my logo.
You can put color into it I am very open on design and color

What my company does is we deal with dealerships that sell equipment such as Dump Trucks garbage trucks tractors trailers. Customers get referred to us and depending on their time in business we will ask for the following items

Companies that have been in business for more than two years we have a credit application program up to 250K . With this program we need the following items Credit application filled out(which is what I would like to be able for the customer to click on my website to get.) as well as three current month bank statements.

Deals over 250k we will need the following items

2 years business tax returns
2 years personal tax returns
Profit & Loss statement
Personal Financial Statement

what we do
100% FINANCING
SEASONAL PAYMENTS
LOAN BALLOON PAYMENTS
TRAC LEASING
LOW-INTEREST REFINANCING RATES
DEBT CONSOLIDATION

We specialize in creative financing solutions and offer a variety of reliable, flexible and expandable lending choices.

Target Market(s)

Trucking Companies

Industry/Entity Type

Trucking Company

Contact Information for Business Card

* $250,000 Application only Program
* Loans from $30,000 to 5,000,000
* Competitive Interest Rates

Font styles to use
Serif
Sans Serif

Colors

Designer to choose colors to be used in the design.

Requirements
Must have
• On the back of the card.
• * $250,000 Application only Program
• * Loans from $30,000 to 5,000,000
• My name, email, website. address
• * Competitive Interest Rates
• * 100% Financing
Nice to have
• I want my logo to pop on the card
• My logo is the great one I would like to use
Should not have
• I am up for your creativity as well

```html
<!DOCTYPE html>
<html lang="en">
<head>
<meta charset="utf-8">
<title>Summit Lending – Business Card</title>
<link href="https://fonts.googleapis.com/css2?family=Open+Sans:wght@400;600;700&display=swap" rel="stylesheet">
<style>
  :root{
    --navy:#0f2a6b;
    --red:#c8102e;
    --white:#ffffff;
    --ink:#1d2a55;
    --muted:#8a93a8;
    --silver:#c9ccd3;
    --backdrop:#3a3330;
  }
  *{box-sizing:border-box;margin:0;padding:0}
  html,body{width:1200px;height:844px;overflow:hidden}
  body{background:var(--backdrop);font-family:"Open Sans",Arial,sans-serif;position:relative}
  .card{position:absolute;width:520px;height:300px;overflow:hidden;box-shadow:0 10px 28px rgba(0,0,0,.45)}
  .card--front{left:50px;top:300px;background:var(--white)}
  .card--back{left:630px;top:300px;background:var(--navy)}

  /* front */
  .brand{position:absolute;right:30px;top:30px;display:flex;align-items:center;gap:10px}
  .brand__mark{width:46px;height:46px;border-radius:50%;background:var(--navy)}
  .brand__name{font-weight:700;font-size:25px;color:var(--navy);letter-spacing:.5px;text-transform:uppercase;line-height:1}
  .front__rule{position:absolute;left:200px;right:30px;top:100px;height:1px;background:var(--muted);opacity:.6}
  .contact{position:absolute;right:30px;top:112px;list-style:none;text-align:right;font-size:13.5px;color:var(--ink);line-height:20px}
  .contact li{display:flex;justify-content:flex-end;align-items:center;gap:6px}
  .contact svg{width:12px;height:12px;fill:var(--navy)}
  .person{position:absolute;left:30px;top:120px;color:var(--ink)}
  .person__name{font-weight:700;font-size:20px;line-height:26px;letter-spacing:.5px;color:var(--navy);text-transform:uppercase}
  .person__name span{color:var(--red)}
  .person__role{font-size:13px;line-height:18px}
  .person__addr{font-size:13px;line-height:17px;margin-top:6px}
  .front__band{position:absolute;left:0;right:0;bottom:0;height:80px;background:var(--navy);color:var(--white);
    display:grid;grid-template-columns:max-content max-content;column-gap:22px;padding:20px 30px 0;
    font-size:13px;line-height:19px;list-style:none;white-space:nowrap}
  .front__band li::before,.services li::before{content:"";display:inline-block;width:6px;height:6px;border-radius:50%;background:currentColor;margin-right:7px;vertical-align:middle}

  /* back */
  .emblem{position:absolute;left:78px;top:50px;width:150px;height:150px;border-radius:50%;
    background:radial-gradient(circle at 40% 35%,#eef0f3,var(--silver) 55%,#8f949e);display:flex;align-items:center;justify-content:center}
  .emblem__name{font-weight:700;font-size:16px;color:var(--navy);text-transform:uppercase;text-align:center;line-height:19px}
  .back__divider{position:absolute;left:270px;top:40px;width:1px;height:150px;background:rgba(255,255,255,.3)}
  .services{position:absolute;left:290px;top:42px;color:var(--white);list-style:none;font-size:11px;line-height:17px;text-transform:uppercase}
  .services__title{font-weight:700;font-size:12px;margin-bottom:3px}
  .back__band{position:absolute;left:0;right:0;bottom:0;height:82px;background:var(--red);color:var(--white);
    font-size:13.5px;line-height:20px;text-align:center;padding-top:20px}
</style>
</head>
<body>
  <section class="card card--front" aria-label="Card front">
    <div class="brand">
      <span class="brand__mark" aria-hidden="true"></span>
      <span class="brand__name">Summit Lending</span>
    </div>
    <div class="front__rule"></div>
    <ul class="contact">
      <li>044-555 010 234
        <svg viewBox="0 0 24 24"><path d="M6.6 10.8a15 15 0 006.6 6.6l2.2-2.2a1 1 0 011-.25 11.4 11.4 0 003.6.6 1 1 0 011 1V20a1 1 0 01-1 1A17 17 0 013 4a1 1 0 011-1h3.5a1 1 0 011 1c0 1.250.2 2.450.6 3.6a1 1 0 01-.25 1z"/></svg></li>
      <li>info@summitlending.com
        <svg viewBox="0 0 24 24"><path d="M2 5h20v14H2z M2 5l10 8 10-8" fill="var(--navy)" stroke="#fff" stroke-width="1.5"/></svg></li>
      <li>www.summitlending.com
        <svg viewBox="0 0 24 24"><circle cx="12" cy="12" r="10"/><path d="M2 12h20M12 2c3 3 3 17 0 20M12 2c-3 3-3 17 0 20" stroke="#fff" stroke-width="1.3" fill="none"/></svg></li>
    </ul>
    <div class="person">
      <h1 class="person__name">Daniel <span>Harper</span></h1>
      <p class="person__role">Managing Director</p>
      <p class="person__addr">88 Harbor Road,<br>20415, Eastland</p>
    </div>
    <ul class="front__band">
      <li>$250,000 Application only Program</li>
      <li>Competitive Interest Rates</li>
      <li>Loans from $30,000 to 5,000,000</li>
      <li>100% Financing</li>
    </ul>
  </section>

  <section class="card card--back" aria-label="Card back">
    <div class="emblem" role="img" aria-label="Company emblem area">
      <span class="emblem__name">Summit<br>Lending</span>
    </div>
    <div class="back__divider"></div>
    <ul class="services">
      <li class="services__title">What We Do</li>
      <li>100% Financing</li>
      <li>Seasonal Payments</li>
      <li>Loan Balloon Payments</li>
      <li>TRAC Leasing</li>
      <li>Low-Interest Refinancing Rates</li>
      <li>Debt Consolidation</li>
    </ul>
    <div class="back__band">
      <p>2 years business tax returns | 2 years personal tax returns</p>
      <p>Profit &amp; Loss statement | Personal Financial Statement</p>
    </div>
  </section>
</body>
</html>
```